BrivoTerna. Lantern of the Steady Harvest. Business card

Professional business card for BrivoTerna (Lantern of the Steady Harvest)
My rationale: Strategy-> Execution-> Results-> Value that lead to the BrivoTerna name: We put the Lantern of the Steady Harvest.
We deliver value to our customers helping them at defining a good strategy (cyan arrow). 90% of well formulated strategies fail due to poor execution so we also consider strategical execution very important (green arrow). Due to the execution we obtain the results (blue arrow). Finally, the results provide feedback to redefine strategy, and the new strategy has to be executed and new results obtained providing new feedback and on and on. It's like a wheel that finally, must create corporate value: value for shareholders, staholders, employees, providers...-

Target Market(s)

CEOs and steering comitees , invewrnent funds

Industry/Entity Type

Business Consultant

Contact Information for Business Card

Teodoro Vinsquel
CEO & Founder
teodoro.vinsquel@brivoterna-example.com
Mobile: +34 655.803.912
www.brivoterna-example.com

Colors

Designer to choose colors to be used in the design.

Requirements
Nice to have
• Nice to hace the words: Strategy, execution, results
• Nice to vave the claim: Lantern of the Steady Harvest
• The three colors should be shown:
• cyan for STRATEGY
• green for EXECUTION
• blue for RESULTS
Should not have
• Complete black background

```html
<!DOCTYPE html>
<html lang="en">
<head>
<meta charset="utf-8">
<title>BrivoTerna — Business Card</title>
<link rel="stylesheet" href="https://fonts.googleapis.com/css2?family=Open+Sans:wght@400;600;700&display=swap">
<style>
  :root {
    --page-bg: #d9dce3;
    --brand-blue: #0b2fa3;
    --brand-navy: #0d2a8a;
    --strategy-cyan: #17a8e6;
    --execution-green: #8cc63f;
    --paper-white: #ffffff;
    --soft-white: #e8eefc;
  }
  * { box-sizing: border-box; margin: 0; padding: 0; }
  html, body {
    width: 1200px; height: 900px; overflow: hidden;
    background: var(--page-bg);
    font-family: "Open Sans", Arial, sans-serif;
  }
  .sheet {
    position: relative; width: 1200px; height: 900px;
    display: flex; flex-direction: column; align-items: center; justify-content: center; gap: 44px;
  }
  .card {
    position: relative; width: 660px; height: 378px;
    border-radius: 22px; overflow: hidden;
    background: var(--brand-blue);
    box-shadow: 0 10px 28px rgba(10, 20, 60, 0.25);
  }
  .card-front .swoosh { position: absolute; inset: 0; width: 100%; height: 100%; }
  .wordmark { font-weight: 700; letter-spacing: -1px; line-height: 1; white-space: nowrap; }
  .card-front .wordmark {
    position: absolute; left: 30px; top: 206px;
    font-size: 40px; color: var(--brand-navy);
  }
  .contact {
    position: absolute; right: 30px; top: 34px; text-align: right; color: var(--paper-white);
  }
  .contact .person { font-size: 20px; font-weight: 700; }
  .contact .role { font-size: 13.5px; margin-top: 2px; }
  .contact-list { list-style: none; margin-top: 28px; font-size: 12.5px; line-height: 1.8; }
  .contact-list li { display: flex; justify-content: flex-end; align-items: center; gap: 7px; white-space: nowrap; }
  .contact-list svg { width: 13px; height: 13px; flex: none; }
  .pillars {
    position: absolute; right: 30px; bottom: 32px; white-space: nowrap;
    font-size: 14px; font-weight: 700; color: var(--strategy-cyan);
  }
  .pillars .dot { color: var(--execution-green); margin: 0 5px; }
  .card-back { display: flex; flex-direction: column; align-items: center; justify-content: center; }
  .card-back .wordmark { font-size: 66px; color: var(--paper-white); margin-top: 10px; }
  .claim {
    display: flex; align-items: center; gap: 12px; margin-top: 30px;
    color: var(--paper-white); font-size: 17px;
  }
  .claim .rule { width: 110px; height: 1px; background: var(--soft-white); opacity: 0.8; }
</style>
</head>
<body>
<main class="sheet">
  <section class="card card-front">
    <svg class="swoosh" viewBox="0 0 660 378" preserveAspectRatio="none" aria-hidden="true">
      <path d="M0 0 L194 0 Q354 120 314 378 L0 378 Z" fill="var(--execution-green)"/>
      <path d="M0 0 L182 0 Q342 120 302 378 L0 378 Z" fill="var(--strategy-cyan)"/>
      <path d="M0 0 L170 0 Q330 120 290 378 L0 378 Z" fill="var(--paper-white)"/>
    </svg>
    <div class="wordmark">BrivoTerna</div>
    <div class="contact">
      <div class="person">Teodoro Vinsquel</div>
      <div class="role">CEO &amp; Founder</div>
      <ul class="contact-list">
        <li>+34 655.803.912
          <svg viewBox="0 0 14 14"><rect x="4" y="1" width="6" height="12" rx="1.2" fill="none" stroke="var(--strategy-cyan)" stroke-width="1.3"/></svg>
        </li>
        <li>teodoro.vinsquel@brivoterna-example.com
          <svg viewBox="0 0 14 14"><rect x="1" y="3" width="12" height="8" rx="1" fill="none" stroke="var(--strategy-cyan)" stroke-width="1.3"/><path d="M1.5 3.5 L7 8 L12.5 3.5" fill="none" stroke="var(--strategy-cyan)" stroke-width="1.3"/></svg>
        </li>
        <li>www.brivoterna-example.com
          <svg viewBox="0 0 14 14"><circle cx="7" cy="7" r="5.6" fill="none" stroke="var(--strategy-cyan)" stroke-width="1.2"/><path d="M1.5 7 H12.5 M7 1.5 C4 4.5 4 9.5 7 12.5 C10 9.5 10 4.5 7 1.5" fill="none" stroke="var(--strategy-cyan)" stroke-width="1"/></svg>
        </li>
      </ul>
    </div>
    <div class="pillars">Strategy<span class="dot">•</span>Execution<span class="dot">•</span>Results</div>
  </section>

  <section class="card card-back">
    <div class="wordmark">BrivoTerna</div>
    <div class="claim"><span class="rule"></span>Lantern of the Steady Harvest<span class="rule"></span></div>
  </section>
</main>
</body>
</html>
```